Climb Past Tuesday - Nobody Writes My Ending

The front book cover. The book will include life lessons I've learned through three breast cancer (Pink Ribbon) diagnoses and how to create positivity through adversity. Lessons that most people don't think of until they're hit with a life-altering setback. The chapters include Imposter Syndrome (Pink Ribbon Warriors don't have time to debate if they're good enough, they just jump in and get it done because life is too short), Stand Your Ground (stick up for your beliefs and advocate for yourself), The Flip Side of It's All About Me (like an emergency rescuer who must equip themselves first, you need to take care of yourself first). The main message in the book is when others say you CAN'T, I say you CAN! Warrior means being strong no matter what life deals you. I've included a word document with more information.
Updates

Please note: Pink is only to be an accent color. I'd like my brand colors to be included. The title of the book is to be the focus with an image to add to the book cover appeal.

Target Market(s)

professionals with a growth mindset and people going through adversity

Industry/Entity Type

HR, Libraries, Hosppitality,

Font styles to use
Sans Serif

Colors
6B429C
8869AF
B7A5CE
E3DAEB
F3F0F8

Requirements
Must have
• Be original. Cover to be appealing to male and female buyers. Incorporate my purple brand color. Be creative and unique.
Nice to have
• Although I have offered a suggestion, I'm open to a creative cover that wows me.
Should not have
• No cartoon image or stock image

```html
<!DOCTYPE html>
<html lang="en">
<head>
<meta charset="utf-8">
<title>Nobody Writes My Ending – Book Cover</title>
<link rel="stylesheet" href="https://fonts.googleapis.com/css2?family=Jost:ital,wght@0,400;0,500;1,500&display=swap">
<style>
  :root {
    --stage: #262626;
    --paper: #ffffff;
    --purple-deep: #633c77;
    --purple-bright: #8e2396;
    --gold: #f0b63f;
    --band-gold: #edb43e;
    --author-purple: #6e2f8a;
    --magenta: #e41fb9;
  }
  html, body {
    margin: 0;
    padding: 0;
    width: 1200px;
    height: 1200px;
    overflow: hidden;
    background: var(--stage);
  }
  .cover {
    position: absolute;
    left: 236px;
    top: 17px;
    width: 728px;
    height: 1165px;
    background: var(--paper);
    overflow: hidden;
    font-family: "Jost", sans-serif;
  }
  .title-disc {
    position: absolute;
    left: -87px;
    top: -374px;
    width: 902px;
    height: 902px;
    border-radius: 50%;
    background: linear-gradient(90deg, var(--purple-deep) 0%, var(--purple-bright) 100%);
  }
  .title {
    position: absolute;
    left: 0;
    top: 0;
    width: 100%;
    margin: 0;
    color: var(--gold);
    text-align: center;
    font-weight: 500;
    text-transform: uppercase;
    line-height: 1;
  }
  .title span { position: absolute; left: 0; width: 100%; display: block; }
  .title .line-1 { top: 44px; font-size: 150px; letter-spacing: -2px; }
  .title .line-2 { top: 200px; font-size: 112px; letter-spacing: -2px; }
  .title .line-3 { top: 318px; font-size: 138px; font-style: italic; letter-spacing: -2px; }
  .hero-image {
    position: absolute;
    left: 20px;
    top: 580px;
    width: 690px;
    height: 500px;
  }
  .subtitle {
    position: absolute;
    left: 0;
    top: 716px;
    width: 100%;
    margin: 0;
    text-align: center;
    color: var(--gold);
    font-weight: 400;
    font-size: 30px;
    line-height: 31px;
    letter-spacing: -1px;
    text-transform: uppercase;
  }
  .subtitle span { display: block; }
  .author-band {
    position: absolute;
    left: 0;
    bottom: 0;
    width: 100%;
    height: 67px;
    background: var(--band-gold);
    color: var(--author-purple);
    font-size: 32px;
    font-weight: 400;
    text-align: center;
    line-height: 67px;
  }
</style>
</head>
<body>
  <main class="cover">
    <div class="title-disc"></div>
    <h1 class="title">
      <span class="line-1">Nobody</span>
      <span class="line-2">Writes My</span>
      <span class="line-3">Ending!</span>
    </h1>

    <svg class="hero-image" viewBox="0 0 690 500" role="img" aria-label="Pink boxing glove punching through torn white paper">
      <defs>
        <radialGradient id="tear-shadow" cx="50%" cy="48%" r="50%">
          <stop offset="0%" stop-color="#bdbdbd"/>
          <stop offset="70%" stop-color="#e6e6e6"/>
          <stop offset="100%" stop-color="#ffffff" stop-opacity="0"/>
        </radialGradient>
        <radialGradient id="glove-tone" cx="50%" cy="45%" r="55%">
          <stop offset="0%" stop-color="#e838c4"/>
          <stop offset="100%" stop-color="#d418ab"/>
        </radialGradient>
      </defs>
      <ellipse cx="340" cy="245" rx="340" ry="230" fill="url(#tear-shadow)"/>
      <ellipse cx="350" cy="247" rx="210" ry="155" fill="url(#glove-tone)"/>
    </svg>

    <p class="subtitle">
      <span>Hard</span>
      <span>Lessons</span>
      <span>From</span>
      <span>A Three-Time</span>
      <span>Survivor</span>
    </p>

    <footer class="author-band">Rae Donnelly, CPCC, MHRM, CDT</footer>
  </main>
</body>
</html>
```